Velora Kestrel Glide Toothbrush Backcard Design

We need a toothbrush backcard (toothbrush packaging) design for our new toothbrush. We are one of the leading toothbrush distributor and producer company. At the moment our toothbrushes are selling at Marvo, Sunway Depot, 9-Twenty and many more supermarkets and mom-and-pop shops in Thailand. Our toothbrush is emphasized on the soft and slim tip bristles which will not hurt your enamel. Easy to grip handle that will ease of use. These 2 mains point should be communicated through the design.

Our brand name is Velora (see attached logo that you can use) and the toothbrush model is Kestrel Glide. We will have 2 series for this model which are Kestrel Glide Extra Soft and Kestrel Glide Medium soft. They are basically differentiated by its packaging colors.

We are looking for the attractive and outstanding design from what available in the market right now. Please see enclosed die cut shape of the packaging. This backcard will hold 3 pieces of toothbrush with clear blister cover.

P.S We are very confident that our product produced with very good quality that's why we want to attract people to try. So when they walk in the aisle we want our toothbrush packaging to be eye catching and welcome customer to try.

Target Market(s)

B+ household consumers age between 18-65 both men and women who has open minded to the new product and willing to spend money without brand royalty.

Font styles to use
Sans Serif

Colors

Designer to choose colors to be used in the design.

Requirements
Must have
• - Logo, and model name
• - Quality mark as following GMP, NHB, ISO9001:2015, ISO22176
• - Attractive character which attract the target clients to try.
• - 2-sided packaging using attached die cut
Nice to have
Should not have
• What other brands have

```html
<!DOCTYPE html>
<html lang="en">
<head>
<meta charset="utf-8">
<title>Velora Kestrel Glide Extra Soft – Backcard</title>
<link rel="stylesheet" href="https://fonts.googleapis.com/css2?family=Montserrat:wght@500;600;700;800;900&family=Great+Vibes&display=swap">
<style>
:root{
  --teal:#1fb5c9;
  --teal-deep:#1596ab;
  --indigo:#35309a;
  --indigo-deep:#262276;
  --yellow:#ffd21a;
  --red:#e8262c;
  --orange:#f26a21;
  --white:#ffffff;
  --ink:#2b2b2b;
  --grey:#e6e6e6;
  --die:#5aa9d6;
  --mint:#8fdcc8;
}
*{margin:0;padding:0;box-sizing:border-box}
html,body{width:961px;height:1200px;overflow:hidden;background:var(--white)}
body{position:relative;font-family:"Montserrat",sans-serif}
.abs{position:absolute}

/* front card */
.front{left:155px;top:128px;width:325px;height:1015px;border-radius:40px;overflow:hidden}
.front-bg{position:absolute;inset:0}
.brand-top{left:64px;top:38px;font-weight:800;font-size:26px;color:var(--white);letter-spacing:.5px}
.vertical{transform-origin:left top;transform:rotate(-90deg);white-space:nowrap}
.model-top{left:32px;top:250px;display:flex;align-items:center;gap:6px}
.model-top .word{font-weight:700;font-size:20px;color:var(--yellow)}
.pill{display:inline-block;background:var(--yellow);color:var(--ink);font-weight:800;border-radius:20px}
.model-top .pill{font-size:9px;padding:2px 7px}
.script{font-family:"Great Vibes",cursive;font-weight:400}
.model-top .script{font-size:26px;color:var(--yellow)}
.badge-stack{left:33px;top:267px;display:flex;flex-direction:column;gap:12px}
.badge{width:26px;border-radius:3px}
.badge.dark{background:var(--ink)}
.badge.light{background:var(--white);border:2px solid var(--ink)}
.brushes{left:106px;top:187px;width:182px;height:780px;border-radius:60px 60px 40px 40px;background:linear-gradient(180deg,#fbfbfb 0%,#f1f3f3 30%,var(--mint) 55%,#e9f6f2 100%);opacity:.95}
.front-ribbon{position:absolute;left:0;top:0;z-index:2}
.ribbon-text{z-index:3;left:48px;top:620px;color:var(--white);font-weight:800;line-height:1.1;white-space:nowrap;transform-origin:left top;transform:rotate(-62deg)}
.ribbon-text .l1{font-size:14px}
.ribbon-text .l2{font-size:20px}
.brand-big{left:38px;top:950px;font-weight:900;font-size:66px;color:var(--white);letter-spacing:1px}
.extra-bottom{left:35px;top:956px;font-size:15px;padding:2px 10px}
.diamond{width:140px;height:140px;background:var(--red);transform:rotate(45deg);border-radius:6px}
.front .diamond{left:130px;top:737px;z-index:4}
.pack{display:flex;flex-direction:column;align-items:center;text-align:center;color:var(--white);transform:translateX(-50%);z-index:5}
.front .pack{left:200px;top:710px}
.pack .num{font-weight:900;font-size:66px;line-height:1}
.pack .line{display:flex;align-items:center;gap:4px;line-height:1}
.pack .model{font-weight:700;font-size:17px;color:var(--yellow)}
.pack .pill{font-size:8px;padding:1px 6px}
.pack .script{font-size:30px;color:var(--yellow);margin-top:-6px}
.pack .label{font-weight:800;font-size:24px;margin-top:-8px}

/* back card */
.back-svg{position:absolute;left:0;top:0}
.brand-back{left:605px;top:297px;font-weight:900;font-size:38px;color:var(--ink);letter-spacing:1px}
.model-back{left:612px;top:370px}
.model-back .word{font-weight:600;font-size:22px;color:var(--ink)}
.model-back .row{display:flex;align-items:center;gap:6px;margin-top:-4px}
.model-back .pill{background:var(--ink);color:var(--white);font-size:10px;padding:2px 8px}
.model-back .script{font-size:34px;color:var(--ink)}
.window{left:605px;top:447px;width:185px;height:350px;background:var(--grey)}
.back-ribbon{position:absolute;left:0;top:0}
.back-ribbon-text{left:598px;top:572px;color:var(--white);font-weight:800;line-height:1.1;white-space:nowrap;transform-origin:left top;transform:rotate(-62deg)}
.back-ribbon-text .l1{font-size:11px}
.back-ribbon-text .l2{font-size:15px}
.back .diamond{left:647px;top:828px;width:100px;height:100px;background:var(--ink)}
.back .pack{left:697px;top:808px}
.back .pack .num{font-size:46px}
.back .pack .model{font-size:12px;color:var(--white);font-weight:600}
.back .pack .pill{background:var(--white);color:var(--ink);font-size:6px}
.back .pack .script{font-size:22px;color:var(--white);margin-top:-4px}
.back .pack .label{font-size:17px;margin-top:-5px}
.badge-row{left:588px;top:964px;display:flex;gap:12px;align-items:center}
.badge-row .badge{height:24px}
.code-box{left:605px;top:1007px;width:185px;height:76px;border:1px solid #9a9a9a;background:var(--white)}
</style>
</head>
<body>

<section class="front abs" aria-label="Front of backcard">
  <svg class="front-bg" width="325" height="1015" viewBox="0 0 325 1015">
    <defs>
      <linearGradient id="tealFill" x1="0" y1="0" x2="1" y2="1">
        <stop offset="0" stop-color="#27c3d4"/><stop offset="1" stop-color="#129aae"/>
      </linearGradient>
      <radialGradient id="silverFill" cx=".55" cy=".45" r=".7">
        <stop offset="0" stop-color="#f4f5f7"/><stop offset=".6" stop-color="#d3d6db"/><stop offset="1" stop-color="#b7bbc2"/>
      </radialGradient>
      <linearGradient id="indigoFill" x1="0" y1="0" x2="0" y2="1">
        <stop offset="0" stop-color="#3a35a6"/><stop offset="1" stop-color="#2a2580"/>
      </linearGradient>
    </defs>
    <rect width="325" height="1015" fill="url(#silverFill)"/>
    <path d="M0,0H325V160Q190,185 0,300Z" fill="url(#tealFill)"/>
    <path d="M0,300Q190,185 325,160" stroke="var(--yellow)" stroke-width="9" fill="none"/>
    <path d="M0,645Q160,560 325,445V1015H0Z" fill="url(#indigoFill)"/>
    <path d="M0,645Q160,560 325,445" stroke="var(--yellow)" stroke-width="8" fill="none"/>
    <rect x="150" y="82" width="162" height="42" rx="10" fill="none" stroke="rgba(255,255,255,.5)" stroke-width="1.5"/>
    <rect x="14" y="52" width="297" height="940" rx="28" fill="none" stroke="rgba(255,255,255,.35)" stroke-width="1.2"/>
  </svg>

  <div class="brand-top abs">Velora</div>

  <div class="model-top abs vertical">
    <span class="word">Kestrel</span>
    <span class="pill">EXTRA</span>
    <span class="script">Glide</span>
  </div>

  <div class="badge-stack abs">
    <div class="badge dark" style="height:38px"></div>
    <div class="badge light" style="height:56px"></div>
    <div class="badge light" style="height:34px"></div>
    <div class="badge dark" style="height:38px"></div>
  </div>

  <div class="brushes abs" role="img" aria-label="Three white toothbrushes with mint green handles under a clear blister"></div>

  <svg class="front-ribbon" width="325" height="1015" viewBox="0 0 325 1015">
    <path d="M5,625Q15,510 120,462Q140,452 148,448L150,500Q100,515 85,590L5,628Z" fill="var(--red)"/>
    <path d="M110,468Q135,452 148,448L150,500Q132,485 110,468Z" fill="var(--orange)"/>
  </svg>
  <div class="ribbon-text abs">
    <div class="l1">Soft &amp; Slim Tip Bristles</div>
    <div class="l2">Easy to Grip</div>
  </div>

  <div class="brand-big abs vertical">VELORA</div>
  <span class="extra-bottom pill abs">EXTRA</span>

  <div class="diamond abs"></div>
  <div class="pack abs">
    <div class="num">3</div>
    <div class="model">Kestrel</div>
    <div class="line"><span class="pill">EXTRA</span><span class="script">Glide</span></div>
    <div class="label">PACK</div>
  </div>
</section>

<section class="back" aria-label="Back of backcard">
  <svg class="back-svg" width="961" height="1200" viewBox="0 0 961 1200">
    <rect x="547.5" y="140.5" width="300" height="992" rx="40" fill="none" stroke="var(--die)" stroke-width="1.2"/>
    <rect x="567.5" y="160.5" width="260" height="950" rx="26" fill="none" stroke="var(--die)" stroke-width="1.2"/>
    <path d="M547,230H565V196H725Q735,196 735,206V250Q735,260 725,260H567V244H547" fill="none" stroke="var(--die)" stroke-width="1.2"/>
    <path d="M575,212H605Q625,212 640,222Q660,235 680,220Q700,205 710,222V238Q710,246 700,246H575Z" fill="none" stroke="var(--die)" stroke-width="1.2"/>
  </svg>

  <div class="brand-back abs">VELORA</div>
  <div class="model-back abs">
    <div class="word">Kestrel</div>
    <div class="row"><span class="pill">EXTRA</span><span class="script">Glide</span></div>
  </div>

  <div class="window abs"></div>
  <svg class="back-ribbon" width="961" height="1200" viewBox="0 0 961 1200">
    <path d="M570,572Q574,468 660,444Q690,437 708,440L702,456Q648,478 642,590Z" fill="var(--ink)"/>
    <path d="M642,590Q648,478 702,456L708,440Q660,475 652,596Z" fill="#5b5b5b"/>
  </svg>
  <div class="back-ribbon-text abs">
    <div class="l1">Soft &amp; Slim Tip Bristles</div>
    <div class="l2">Easy to Grip</div>
  </div>

  <div class="diamond abs"></div>
  <div class="pack abs">
    <div class="num">3</div>
    <div class="model">Kestrel</div>
    <div class="line"><span class="pill">EXTRA</span><span class="script">Glide</span></div>
    <div class="label">PACK</div>
  </div>

  <div class="badge-row abs">
    <div class="badge dark" style="width:44px"></div>
    <div class="badge light" style="width:30px"></div>
    <div class="badge light" style="width:64px"></div>
    <div class="badge dark" style="width:44px"></div>
  </div>

  <div class="code-box abs"></div>
</section>

</body>
</html>
```